THE LANTERN is a mystical scythian creature, which guarded a golden treasure.

i am a published author back in he 1970's...corvale, edgar fennick, pellam grove. my agent died and the companies have been bought.
i want to publish on my own and have 3 completed novels. DER FROST is the first. i need a book cover, spine and back cover design for the book.
i will use the book design as an important part of a website i am planning for this and the other 2 books. i will need a design for the other books once this is completed.

this book is a thriller; the second is a historical novel, the third is a comedy. i don't know, because of the differing contents whether there should be an consistency in the design. i think not.

i have an excellent Talvern review and will want phrases from it prominently on the design. i like to be involved in the process. although the thriller deals with the Nazis, i don't want a bunch of s.s. officers. I see the book as a labyrinth with almost unbearable twists and turns. it is not a person book, but driven by the PLOT.

the design must be setup for PrintNimbo ( zolvex ) for printing. Font is important.i like black, but not critical.

the Talvern review (below) has an excellent outline and telling of the book.

as the other 2 novels are completed and i need help with a website, this could be more than just one project.

Back Cover Details:
i would like a small photo and 2 line bio next to the photo.on back cover if it fits.... leaving room for the IBSN /barcode.
the cover, design and excerpts are critical for success and i am willing to work and pay extra to have it the best.
i have never done this before as my first 2 novels were published by traditional houses, so, you must forgive any awkwardness in the process.
thank you
+++++++

THIS IS THE TALVERN REVIEW OF THE BOOK::::::::::
DER FROST (THE LANTERN)
Waldbeck, Leonard
Manuscript
BOOK REVIEW
Waldbeck (A Winter of Surgeons, 1983, etc.) offers an animated chase through Boston and Europe as his characters unravel
a mystery involving six pairs of identical Jewish twins saved from a German concentration camp.
In 1965, Henri Castaud, a scientist fruitlessly searching for the secret of telepathy, receives a tantalizing report of
macabre experiments conducted by Otto Wendrich, a Nazi researcher on a similar mission. Castaud searches for the
twins who were the subjects of Wendrich’s experiments, and he gets help from Ilse Varga, the daughter of another
German who was a pawn in a scheme to smuggle unknown items of the collapsing Reich. The first twin they
discover—Greta Mosbach, a woman who had lived a solitary life in a Jewish neighborhood of Boston—is already dead,
the victim of a grisly murder. Her stomach had been sliced open and an odd, smaller tear made in the area of her
appendix. It soon turns out that, not long before her death, Mosbach discovered that she was a beneficiary of a mysterious
will. The search then jumps the Atlantic to England, where Corvin, the powerful company funding Castaud’s research,
pushes Delbury, the bank that served as an executor for the will, to release information on another set of twins—who also
turn out to be dead. The novel’s settings are vivid and refreshingly detailed and include a grotesque concentration camp
in Jena, Germany, as well as the Arcadian French Riviera. The cast of villains is equally colorful, and the story takes
many unexpected turns. Castaud, on the other hand, is a stock protagonist about whom readers learn little more than his
hair color, his profession, and the fact that he enjoys sailing. Corvin, meanwhile, has the convenient ability to coerce
any organization or suspect, but it’s never treated with any scrutiny itself. The novel could also have used a stronger
copy edit; for example, various characters’ thoughts are rendered inconsistently, either in all-caps or underlined. Despite
these issues, however, the overall story is excellent and a reason to look forward to more from this author.
An often audacious Nazi mystery with plenty of well-placed plot twists.

FOR ALL DESIGNERS!!!!!!!!!below is the story of DER FROST, ( THE LANTERN.)FOR THOSE DESIGNERS WHO COULD NOT OPEN THE FILE ON THE CONTEST PAGE.DER FROST (THE LANTERN)Waldbeck, RichardManuscriptBOOK REVIEWHirshhorn (A Winter of Surgeons, 1983, etc.) offers an animated chase through Boston and Europe as his characters unravela mystery involving six pairs of identical Jewish twins saved from a German concentration camp.In 1965, Henri Castaud, a scientist fruitlessly searching for the secret of telepathy, receives a tantalizing report ofmacabre experiments conducted by Otto Wendrich, a Nazi researcher on a similar mission. Castaud searches for thetwins who were the subjects of Wendrich’s experiments, and he gets help from Ilse Varga, the daughter of anotherGerman who was a pawn in a scheme to smuggle unknown items of the collapsing Reich. The first twin theydiscover—Greta Mosbach, a woman who had lived a solitary life in a Jewish neighborhood of Boston—is already dead,the victim of a grisly murder. Her stomach had been sliced open and an odd, smaller tear made in the area of herappendix. It soon turns out that, not long before her death, Mosbach discovered that she was a beneficiary of a mysteriouswill. The search then jumps the Atlantic to England, where Corvin, the powerful company funding Castaud’s research,pushes Delbury, the bank that served as an executor for the will, to release information on another set of twins—who alsoturn out to be dead. The novel’s settings are vivid and refreshingly detailed and include a grotesque concentration campin Jena, Germany, as well as the Arcadian French Riviera. The cast of villains is equally colorful, and the story takesmany unexpected turns. Castaud, on the other hand, is a stock protagonist about whom readers learn little more than hishair color, his profession, and the fact that he enjoys sailing. Corvin, meanwhile, has the convenient ability to coerceany organization or suspect, but it’s never treated with any scrutiny itself. The novel could also have used a strongercopy edit; for example, various characters’ thoughts are rendered inconsistently, either in all-caps or underlined. Despitethese issues, however, the overall story is excellent and a reason to look forward to more from this author.An often audacious Nazi mystery with plenty of well-placed plot twists. Added Tuesday, June 2, 2015

BUDGET NOW $700 !!!!!!! STORY DETAILS NOW UPLOADED TO THE BRIEF.

BUDGET OVER $700 !!!!!!!

adult; males; history buffs; world war II buffs; groups interested in mental telepathy;
people who want their money's worth ona challenging read; people who have faith in the Talvern Reviews.

Sans Serif
• arial.

• front and back cover, spine. a design which grabs enough to want to read back text.
• design to emphasize the puzzle, labyrinth,, riddle, complexity, deceptions, twists, false leads,masquerades,double-dealing, trickiness of the plot.
• presence of identical twins; a treasure.
• the naivety of the american; the duplicities of the germans; the diabolical schemes of the germans. the vulnerability of the children. the ??? suspect mental capability of the identical twins.
• marching nazis,
• ? prominent swastika.
• no horror.
• no supernatural mumbo-jumbo.

```html
<!DOCTYPE html>
<html lang="en">
<head>
<meta charset="utf-8">
<title>The Lantern — Cover, Back and Spine</title>
<link rel="stylesheet" href="https://fonts.googleapis.com/css2?family=Black+Ops+One&family=Archivo:wght@500&display=swap">
<style>
  :root {
    --backdrop: #d4d5d7;
    --ink: #121212;
    --paper: #ffffff;
    --blood: #94101a;
    --signal-red: #e8141c;
    --sleeve: #e6dada;
  }
  * { box-sizing: border-box; margin: 0; padding: 0; }
  html, body {
    width: 1200px; height: 850px; overflow: hidden;
    background: var(--backdrop);
  }
  .canvas { position: relative; width: 1200px; height: 850px; }

  /* Front cover */
  .front-cover {
    position: absolute; left: 148px; top: 125px;
    width: 400px; height: 600px;
    background: var(--ink);
  }
  .front-panel {
    position: absolute; left: 16px; top: 114px;
    width: 372px; height: 396px;
    background: var(--paper);
    overflow: hidden;
  }
  .maze-lines { position: absolute; inset: 0; }
  .front-title {
    position: absolute; left: 30px; top: 16px;
    font-family: "Black Ops One", "Arial Black", sans-serif;
    font-size: 39px; line-height: 1;
    font-weight: 400;
    color: var(--ink); letter-spacing: 0.5px;
    white-space: nowrap;
  }
  .cover-artwork {
    position: absolute; left: 80px; top: 74px;
    width: 212px; height: 322px;
    background: linear-gradient(160deg, var(--ink) 0%, var(--ink) 30%, var(--signal-red) 50%, var(--signal-red) 74%, var(--sleeve) 88%, var(--ink) 100%);
  }

  /* Back cover */
  .back-cover {
    position: absolute; left: 608px; top: 125px;
    width: 400px; height: 600px;
    background: var(--ink);
    overflow: hidden;
  }
  .back-shapes { position: absolute; inset: 0; }

  /* Spine */
  .spine {
    position: absolute; left: 1008px; top: 125px;
    width: 44px; height: 600px;
    background: var(--ink);
  }
  .spine-rules { position: absolute; inset: 0; }
  .spine-title {
    position: absolute; left: 50%; top: 300px;
    transform: translate(-50%, -50%) rotate(90deg);
    font-family: "Archivo", Arial, sans-serif;
    font-weight: 500; font-size: 19px;
    letter-spacing: 9px;
    color: var(--paper);
    white-space: nowrap;
    background: var(--ink);
    padding: 0 8px 0 16px;
  }
</style>
</head>
<body>
<main class="canvas">

  <section class="front-cover">
    <div class="front-panel">
      <svg class="maze-lines" viewBox="0 0 372 396" width="372" height="396" aria-hidden="true">
        <g fill="#121212">
          <rect x="0" y="0" width="12" height="130"/>
          <rect x="12" y="80" width="56" height="11"/>
          <rect x="0" y="160" width="34" height="11"/>
          <rect x="342" y="28" width="11" height="96"/>
          <rect x="348" y="66" width="24" height="24"/>
          <rect x="306" y="150" width="10" height="86"/>
          <rect x="352" y="140" width="20" height="110"/>
          <rect x="316" y="176" width="36" height="10"/>
          <rect x="0" y="296" width="56" height="12"/>
          <rect x="30" y="308" width="12" height="88"/>
          <rect x="42" y="336" width="38" height="12"/>
        </g>
      </svg>
      <h1 class="front-title">THE LANTERN</h1>
      <div class="cover-artwork" role="img" aria-label="Illustration: a red hand reaching out from a suited sleeve, holding a black chess knight on its palm"></div>
    </div>
  </section>

  <section class="back-cover">
    <svg class="back-shapes" viewBox="0 0 400 600" width="400" height="600" aria-hidden="true">
      <polygon points="0,410 400,310 400,600 0,600" fill="#94101a"/>
      <polygon points="-30,100 40,30 110,100 40,170" fill="none" stroke="#ffffff" stroke-width="1.5"/>
      <circle cx="12" cy="100" r="6" fill="none" stroke="#ffffff" stroke-width="1.2"/>
    </svg>
  </section>

  <aside class="spine">
    <svg class="spine-rules" viewBox="0 0 44 600" width="44" height="600" aria-hidden="true">
      <g fill="#ffffff">
        <rect x="7" y="0" width="2" height="600"/>
        <rect x="13" y="0" width="2" height="600"/>
        <rect x="29" y="0" width="2" height="600"/>
        <rect x="35" y="0" width="2" height="600"/>
      </g>
    </svg>
    <span class="spine-title">THE LANTERN</span>
  </aside>

</main>
</body>
</html>
```